Ashmoor Web Design Project

I need the front page and an internal page designed for this client's website. The logo is attached. Obviously the colors have to go with and/or work with the logo colors. I also attached a very rough brochure layout to help you see the direction we're going in with print materials. The rough site map is also attached. I see a slider on the homepage, the art for which I may come back to you to create. This clinic is in a very high end Dallas neighborhood. The hook is that it's a primary care and urgent facility with convenient hours.

I don't know how much this impacts your design, but this will be a Wordpress site and I'm using a framework called Brovila (brovila.com). If Brovila proves to be inflexible, I'll have to get a template that allows me to execute your design.

This site (http://lanternvaleclinic.com) has the type and quality of content I will eventually have on the Ashmoor site.

I just revised the brief for this project. I added the site map and added details to the overview and the "Must Have" section. Thank you for revisiting the brief. 

Reason: Christmas was a bad time to end it.

Target Market(s)

Women 25-54 with children living at home, income over $150k/year

Industry/Entity Type

Clinic

Requirements
Must have
• Masthead incorporating the logo
Followed by the primary nav
Slider on the home page below that
Dual nav - 1 with the nav in the attached site map
2 secondary nav with areas of healthcare
There will three blocks under the nav
1. It's about time (with a small blurb less than 50 words.
2. It's about choices (with small blurb)
3. It's about you (with small blurb)
Three footer blocks
patient check in link on every page
"No appointment? No problem" icon on every page

```html
<!DOCTYPE html>
<html lang="en">
<head>
<meta charset="utf-8">
<title>Ashmoor Medical</title>
<link href="https://fonts.googleapis.com/css2?family=Open+Sans:wght@400;600;700&family=Oswald:wght@500&family=Lato:wght@400&display=swap" rel="stylesheet">
<style>
:root{
  --green:#1fae4b;
  --blue:#0a5aa0;
  --navy:#053a66;
  --stripe:#2a4a98;
  --ink:#1a2a5a;
  --grey:#ececec;
  --text:#333;
  --red:#d0102a;
  --map:#e6e2da;
}
*{margin:0;padding:0;box-sizing:border-box}
html,body{width:1164px;height:1200px;overflow:hidden}
body{position:relative;background:#fff;font-family:"Open Sans",sans-serif;color:var(--text)}
.abs{position:absolute}
.topbar{left:0;top:0;width:1164px;height:35px;background:var(--green)}
.social{top:4px;width:26px;height:26px;border-radius:4px;background:#fff;opacity:.85}
.header{left:0;top:35px;width:1164px;height:112px;background:#fff}
.brand{left:175px;top:60px;display:flex;align-items:center;gap:10px}
.brand-mark{width:58px;height:58px;border-radius:50%;background:var(--blue)}
.brand-name{font-weight:700;font-size:35px;color:var(--blue);letter-spacing:-.5px;line-height:1}
.tagline{left:244px;top:106px;font-size:12.5px;font-weight:600;color:#333;display:flex;align-items:center;gap:5px}
.tagline::before,.tagline::after{content:"";width:34px;height:1px;background:#333}
.account{right:188px;top:72px;font-size:11.5px;color:#555;display:flex;gap:15px}
.mainnav{left:0;top:147px;width:1164px;height:35px;background:var(--blue);border-bottom:1px solid #4d86c0}
.mainnav ul{list-style:none;display:flex;gap:25px;position:absolute;left:185px;top:10px}
.mainnav li{color:#fff;font-weight:700;font-size:11.5px;letter-spacing:.6px}
.slider-band{left:0;top:182px;width:1164px;height:294px;background:var(--stripe)}
.slide{left:173px;top:183px;width:818px;height:293px;border:2px solid var(--green);background:linear-gradient(110deg,#7a8c4a,#a7b86a 40%,#6f8e3e 70%,#4e6e2c)}
.arrow{top:307px}
.slide-box{left:635px;top:207px;width:305px;height:224px;background:rgba(31,174,75,.88);border:1px solid #8fe0a2;padding:26px 10px 0 16px}
.slide-box p{font-family:"Lato",sans-serif;font-size:17.5px;line-height:25px;color:#fff}
.learn{left:816px;top:385px;width:107px;height:24px;border-radius:4px;background:var(--blue);border:1px solid #fff;color:#fff;font-size:11px;text-align:center;line-height:22px}
.dots{left:905px;top:454px;display:flex;gap:4px}
.dots span{width:13px;height:13px;border:1px solid #ccc;background:#444;color:#fff;font-size:8px;text-align:center;line-height:11px}
.dots span.on{background:#fff;color:#333}
.content-band{left:173px;top:476px;width:818px;height:381px;background:var(--grey)}
.side{left:173px;top:476px;width:219px;height:377px;background:#f6f6f6}
.care-list{list-style:none;position:absolute;left:200px;top:489px;width:176px}
.care-list li{height:28.5px;border-bottom:1px dashed #aaa;font-family:"Oswald",sans-serif;font-weight:500;font-size:13.5px;color:var(--ink);padding-left:12px;position:relative;line-height:24px}
.care-list li::before{content:"";position:absolute;left:1px;top:8px;width:6px;height:6px;border-top:2px solid var(--red);border-right:2px solid var(--red);transform:rotate(45deg)}
.video{left:185px;top:720px;width:193px;height:117px;border:3px solid #ccc;background:linear-gradient(135deg,#8a8572,#5d5a4c);box-shadow:2px 3px 4px rgba(0,0,0,.35)}
.play{left:254px;top:752px}
.main{left:403px;top:476px;width:588px;height:377px;background:#fff}
.card{top:487px;width:177px;height:359px;border:1px solid #ddd;background:#fff}
.card-photo{width:175px;height:171px;background:linear-gradient(160deg,#8fae63,#c8b79a 50%,#6f8d4a)}
.card-title{height:27px;background:linear-gradient(#5ac77a,#28a24d);color:#fff;font-family:"Oswald",sans-serif;font-weight:500;font-size:15px;text-align:center;line-height:27px;letter-spacing:.3px}
.card p{padding:18px 9px 0;font-size:10.5px;line-height:14.7px;text-align:justify;letter-spacing:.3px}
.footer{left:0;top:857px;width:1164px;height:343px;background:var(--navy)}
.foot-h{font-size:18px;color:#fff;top:867px;font-weight:400}
.sitemap{list-style:none;position:absolute;left:189px;top:894px}
.sitemap li{font-size:11px;color:#fff;height:16.4px;letter-spacing:.4px}
.map{left:417px;top:897px;width:248px;height:211px;background:linear-gradient(160deg,#ece8e0,#dcd7cc);border:1px solid #fff}
.contact{left:755px;top:892px;font-size:11px;color:#fff;letter-spacing:.4px;line-height:24.2px}
.copyline{left:0;top:1164px;width:1164px;height:1px;background:#3a6c98}
.copy{left:0;top:1175px;width:1164px;text-align:center;font-size:9px;color:#cfd9e6}
</style>
</head>
<body>
<div class="abs topbar"></div>
<div class="abs social" style="left:876px"></div>
<div class="abs social" style="left:914px"></div>
<div class="abs social" style="left:952px"></div>

<header class="abs header"></header>
<div class="abs brand"><span class="brand-mark"></span><span class="brand-name">AshmoorMedical</span></div>
<div class="abs tagline">Immediate Family and Personal Care</div>
<div class="abs account"><span>Register</span><span>Log In</span><span>Blog</span></div>

<nav class="abs mainnav"><ul><li>HOME</li><li>ABOUT US</li><li>SERVICES</li><li>STAFF</li><li>INSURANCE</li><li>VIDEOS</li><li>CONTACT US</li></ul></nav>

<div class="abs slider-band"></div>
<div class="abs slide" role="img" aria-label="Smiling family of four lying on green grass outdoors"></div>
<svg class="abs arrow" style="left:184px" width="28" height="38" viewBox="0 0 28 38"><polyline points="24,3 6,19 24,35" fill="none" stroke="#fff" stroke-width="6"/></svg>
<svg class="abs arrow" style="left:950px" width="28" height="38" viewBox="0 0 28 38"><polyline points="4,3 22,19 4,35" fill="none" stroke="#fff" stroke-width="6"/></svg>
<div class="abs slide-box"><p>Lorem ipsum dolor sit amet consec-tetuer adipiscing elit. Nam cursus. Morbi ut mi. Lorem ipsum dolor sit amet consectetuer adipiscing elit. Nam cursus. Morbi ut mi.</p></div>
<div class="abs learn">Learn more</div>
<div class="abs dots"><span>1</span><span class="on">2</span><span>3</span><span>4</span></div>

<div class="abs content-band"></div>
<div class="abs side"></div>
<ul class="care-list">
  <li>IMMEDIATE CARE</li><li>ALLERGIES</li><li>PRIMARY CARE</li><li>WOMEN’S HEALTH</li><li>MEDICAL SPA TREATMENTS</li><li>MEN’S HEALTH</li><li style="border-bottom:none">WEIGHT LOSS</li>
</ul>
<div class="abs video" role="img" aria-label="Video still of an older couple outdoors"></div>
<svg class="abs play" width="56" height="42" viewBox="0 0 56 42"><rect width="56" height="42" rx="6" fill="rgba(40,40,40,.75)"/><polygon points="22,10 22,32 39,21" fill="#ddd"/></svg>

<div class="abs main"></div>
<article class="abs card" style="left:417px">
  <div class="card-photo" role="img" aria-label="Parents with two children embracing outdoors"></div>
  <div class="card-title">IT’S ABOUT TIME</div>
  <p>Lorem ipsum dolor sit amet consectetuer adipiscing elit. Nam cursus. Morbi ut mi Nullam enim leo, egestas id condimentum at, laoreet mattis, massa. Sed eleifend nonummy diam. Praesent mauris ante, elementum et bibendum atposuere amet.</p>
</article>
<article class="abs card" style="left:608px">
  <div class="card-photo" role="img" aria-label="Mother and daughter sitting in a sunny meadow"></div>
  <div class="card-title">IT’S ABOUT CHOICES</div>
  <p>Lorem ipsum dolor sit amet consectetuer adipiscing elit. Nam cursus. Morbi ut mi Nullam enim leo, egestas id condimentum at, laoreet mattis, massa. Sed eleifend nonummy diam. Praesent mauris ante, elementum et bibendum atposuere amet.</p>
</article>
<article class="abs card" style="left:800px">
  <div class="card-photo" role="img" aria-label="Smiling couple outdoors, woman resting on man's back"></div>
  <div class="card-title">IT’S ABOUT YOU</div>
  <p>Lorem ipsum dolor sit amet consectetuer adipiscing elit. Nam cursus. Morbi ut mi Nullam enim leo, egestas id condimentum at, laoreet mattis, massa. Sed eleifend nonummy diam. Praesent mauris ante, elementum et bibendum atposuere amet.</p>
</article>

<footer class="abs footer"></footer>
<h3 class="abs foot-h" style="left:185px">Sitemap</h3>
<ul class="sitemap">
  <li>Home</li><li>About Us</li><li>Services</li><li>Staff</li><li>Insurance</li><li>Videos</li><li>Immediate Care</li><li>Allergies</li><li>Primary Care</li><li>Women’s Health</li><li>Medical Spa Treatments</li><li>Men’s Health</li><li>Weight Loss</li><li>Contact Us</li>
</ul>
<h3 class="abs foot-h" style="left:417px">Location</h3>
<div class="abs map" role="img" aria-label="Street map showing the clinic location"></div>
<h3 class="abs foot-h" style="left:753px">Contact Us</h3>
<div class="abs contact">
  AshmoorFamilyMedical<br>
  4120 Ashmoor Ave (at Elm Pkwy) Ste<br>
  210, Dallas, TX 75230<br><br>
  Tel: (555) 214 0188<br>
  Fax: (555) 214 0188<br>
  E-mail: info@ashmoorfamilymedical.com
</div>
<div class="abs copyline"></div>
<div class="abs copy">Copyright 2012 AshmoorFamilyMedical. All rights reserved.</div>
</body>
</html>
```